Willow Landing - Multifamily Development

Willow Landing is a Luxury Multifamily Development project located in Orange, NJ. This project will be completed in three phases with the first phase about 75% complete. Each phase will have a different name as follows
CEDAR Willow Landing
LANTERN Willow Landing
BRAMBLEWOOD Willow Landing
We are going to install a banner on the side of the first building which will act as advertising for all buildings. We will eventually need advertising that will be in the windows as well as marketing materials . We want the marketing for this project to be similar for all three phases. At the moment, we are starting with this first simple banner. Attached is a rough idea of the look as well as our color palette. If you feel the color palette is a little too monochrome, feel free to propose an accent color. You can also visit our website to see more info on our company as well as the project. www.tarnlv.com Finally, if you need AI files (ie. for the logo), we can send to you. Thanks..

```html
<!DOCTYPE html>
<html lang="en">
<head>
<meta charset="utf-8">
<title>Willow Landing – Luxury Apartment Rentals</title>
<link rel="stylesheet" href="https://fonts.googleapis.com/css2?family=Montserrat:wght@400;600;700;800&display=swap">
<style>
  :root {
    --brand-blue: #2b6fa8;
    --brand-blue-fade: rgba(43, 111, 168, 0);
    --contact-navy: #2c5a87;
    --ink: #231f20;
    --panel-grey: #ececec;
    --facade-light: #ebebec;
    --facade-mid: #d6d7d9;
    --room-window: #f3f6fa;
    --room-wall: #efebe8;
    --room-warm: #e2d6cc;
    --room-wood: #b99a7e;
    --room-shadow: #5d6158;
    --white: #ffffff;
  }
  html, body {
    margin: 0;
    padding: 0;
    width: 900px;
    height: 1200px;
    overflow: hidden;
    background: var(--white);
  }
  .banner {
    position: relative;
    width: 900px;
    height: 1200px;
    overflow: hidden;
    font-family: "Montserrat", sans-serif;
  }
  .banner__art {
    position: absolute;
    inset: 0;
    width: 900px;
    height: 1200px;
  }
  .brand-name {
    position: absolute;
    left: 52px;
    top: 92px;
    margin: 0;
    font-weight: 700;
    color: var(--ink);
    line-height: 1;
  }
  .brand-name__word {
    display: block;
    font-size: 78px;
    letter-spacing: 2px;
  }
  .brand-name__sub {
    display: block;
    margin-top: 12px;
    margin-left: 2px;
    font-size: 19px;
    letter-spacing: 11.5px;
  }
  .headline {
    position: absolute;
    left: 26px;
    top: 612px;
    margin: 0;
    color: var(--white);
  }
  .headline__project {
    display: block;
    font-size: 40px;
    font-weight: 400;
    line-height: 1;
    letter-spacing: 0.5px;
    margin-bottom: 14px;
  }
  .headline__main {
    display: block;
    font-size: 70px;
    font-weight: 800;
    line-height: 74px;
    letter-spacing: -0.5px;
  }
  .contact {
    position: absolute;
    left: 493px;
    color: var(--contact-navy);
  }
  .contact--phone { top: 1033px; }
  .contact--web { top: 1120px; }
  .contact__label {
    position: absolute;
    left: 59px;
    top: 4px;
    margin: 0;
    font-size: 18.5px;
    font-weight: 400;
    white-space: nowrap;
  }
  .contact__value {
    position: absolute;
    left: 57px;
    top: 30px;
    margin: 0;
    font-size: 25px;
    font-weight: 700;
    white-space: nowrap;
  }
  .contact--web .contact__label { top: 0; }
  .contact--web .contact__value { left: 60px; top: 33px; }
</style>
</head>
<body>
<main class="banner">
  <svg class="banner__art" viewBox="0 0 900 1200" xmlns="http://www.w3.org/2000/svg">
    <defs>
      <linearGradient id="facadeTone" x1="0" y1="0" x2="0" y2="1">
        <stop offset="0" stop-color="var(--facade-light)"/>
        <stop offset="0.45" stop-color="var(--facade-mid)"/>
        <stop offset="1" stop-color="var(--facade-light)"/>
      </linearGradient>
      <linearGradient id="roomTone" x1="0" y1="0" x2="1" y2="0">
        <stop offset="0" stop-color="#e4e8ee"/>
        <stop offset="0.45" stop-color="var(--room-window)"/>
        <stop offset="0.7" stop-color="var(--room-wall)"/>
        <stop offset="1" stop-color="var(--room-warm)"/>
      </linearGradient>
      <radialGradient id="roomShade" cx="840" cy="700" r="170" gradientUnits="userSpaceOnUse">
        <stop offset="0" stop-color="var(--room-shadow)" stop-opacity="0.75"/>
        <stop offset="1" stop-color="var(--room-shadow)" stop-opacity="0"/>
      </radialGradient>
      <radialGradient id="roomWood" cx="820" cy="880" r="190" gradientUnits="userSpaceOnUse">
        <stop offset="0" stop-color="var(--room-wood)" stop-opacity="0.9"/>
        <stop offset="1" stop-color="var(--room-wood)" stop-opacity="0"/>
      </radialGradient>
      <radialGradient id="roomLight" cx="520" cy="520" r="260" gradientUnits="userSpaceOnUse">
        <stop offset="0" stop-color="var(--white)" stop-opacity="0.9"/>
        <stop offset="1" stop-color="var(--white)" stop-opacity="0"/>
      </radialGradient>
      <linearGradient id="blueWash" x1="0" y1="0" x2="900" y2="0" gradientUnits="userSpaceOnUse">
        <stop offset="0" stop-color="var(--brand-blue)"/>
        <stop offset="0.26" stop-color="var(--brand-blue)"/>
        <stop offset="0.55" stop-color="var(--brand-blue-fade)"/>
      </linearGradient>
      <clipPath id="roomClip">
        <path d="M0,434 L215,434 C270,434 300,405 330,350 C370,270 400,182 470,182 L900,182 L900,912 L490,912 C440,912 415,945 385,1000 C350,1070 320,1107 270,1107 L0,1107 Z"/>
      </clipPath>
    </defs>

    <rect class="backdrop-photo" x="0" y="0" width="900" height="1200" fill="url(#facadeTone)" role="img" aria-label="Faded photo of the apartment building facade and street"/>

    <g class="room-photo" clip-path="url(#roomClip)" role="img" aria-label="Photo of a bright apartment living room with a tall blind-covered window and a TV on a wooden console">
      <rect x="0" y="182" width="900" height="925" fill="url(#roomTone)"/>
      <rect x="0" y="182" width="900" height="925" fill="url(#roomLight)"/>
      <rect x="0" y="182" width="900" height="925" fill="url(#roomShade)"/>
      <rect x="0" y="182" width="900" height="925" fill="url(#roomWood)"/>
    </g>
    <path class="blue-band"
          d="M0,434 L215,434 C270,434 300,405 330,350 C370,270 400,182 470,182 L900,182 L900,912 L490,912 C440,912 415,945 385,1000 C350,1070 320,1107 270,1107 L0,1107 Z"
          fill="url(#blueWash)"/>

    <path class="contact-panel"
          d="M900,982 L520,982 C490,982 470,995 450,1022 L368,1140 C350,1170 360,1200 395,1200 L900,1200 Z"
          fill="var(--panel-grey)"/>

    <g class="icon-phone" transform="translate(493,1033)">
      <rect x="0" y="0" width="40" height="71" rx="5" fill="var(--contact-navy)"/>
      <rect x="42" y="0" width="2" height="71" fill="var(--contact-navy)"/>
      <path d="M12,22 C10,26 12,36 18,44 C23,50 27,52 30,51 L32,47 L27,43 L24,45 C21,42 18,37 17,32 L20,30 L18,23 Z" fill="var(--white)"/>
    </g>
    <g class="icon-globe" transform="translate(516,1143)" fill="none">
      <circle cx="0" cy="0" r="24" fill="var(--contact-navy)"/>
      <ellipse cx="0" cy="0" rx="11" ry="24" stroke="var(--panel-grey)" stroke-width="2"/>
      <line x1="0" y1="-24" x2="0" y2="24" stroke="var(--panel-grey)" stroke-width="2"/>
      <line x1="-24" y1="0" x2="24" y2="0" stroke="var(--panel-grey)" stroke-width="2"/>
      <line x1="-21" y1="-11" x2="21" y2="-11" stroke="var(--panel-grey)" stroke-width="2"/>
      <line x1="-21" y1="11" x2="21" y2="11" stroke="var(--panel-grey)" stroke-width="2"/>
    </g>
  </svg>

  <p class="brand-name">
    <span class="brand-name__word">TARN</span>
    <span class="brand-name__sub">PROPERTIES</span>
  </p>

  <h1 class="headline">
    <span class="headline__project">WILLOW LANDING</span>
    <span class="headline__main">LUXURY</span>
    <span class="headline__main">APARTMENT</span>
    <span class="headline__main">RENTALS</span>
  </h1>

  <div class="contact contact--phone">
    <p class="contact__label">More information call us</p>
    <p class="contact__value">973-555-0184</p>
  </div>

  <div class="contact contact--web">
    <p class="contact__label">Visit our website</p>
    <p class="contact__value">https://www.tarnlv.com/</p>
  </div>
</main>
</body>
</html>
```